SnackOrbit!!! A Vending Machine Business Looking for an attractive website.

We are a vending machine business in Northern Michigan. We have changed our name and have rebranded our company. We would like an attractive website that shares who we are, what services we provide, the products we offer in our machines, along with a form businesses can fill out to see if they are a good fit for our company. I would like to have a Home Page, About SnackOrbit, Why Choose SnackOrbit?, Products & Services, Contact Us (With a Login Option), and a page with a questionnaire for thos interested in getting a FREE Vending Machine.

Target Market(s)

Businesses, Campgrounds, Schools, and many more in Northern Michigan

Industry/Entity Type

Vending Machines

Coding

Coded - Design and coding required

Number of Pages Required

5+ page

Requirements
Must have
• An inviting and enticing Home Page. I want to get my potential clients engaged in our website.
Nice to have
• Possibly background photos from Northern Michigan
Should not have
• A corporate feel. I do not want a boring website.

```html
<!DOCTYPE html>
<html lang="en">
<head>
<meta charset="utf-8">
<title>SnackOrbit – Vending in Northern Michigan</title>
<link href="https://fonts.googleapis.com/css2?family=Roboto+Slab:wght@400;500;600;700&family=Lato:wght@400;700&display=swap" rel="stylesheet">
<style>
:root{
  --green:#2d5a2b;
  --green-soft:#a3b5a0;
  --navy:#1c1f5a;
  --navy-band:#232a6e;
  --text:#3a3a3a;
  --white:#ffffff;
  --line:#c9c9c9;
}
*{box-sizing:border-box;margin:0;padding:0}
html,body{width:1200px;height:4020px;overflow:hidden;background:var(--white)}
body{position:relative;font-family:"Roboto Slab",serif;color:var(--text)}
.abs{position:absolute}
.center{text-align:center}
.btn{position:absolute;display:flex;align-items:center;justify-content:center;background:var(--green);color:var(--white);font-family:"Roboto Slab",serif;font-weight:600;font-size:15px;text-decoration:none}
.heading{font-family:"Roboto Slab",serif;font-weight:600;color:var(--navy);font-size:47px;line-height:1}

/* hero */
.hero{position:absolute;left:0;top:0;width:1200px;height:615px}
.hero-photo{position:absolute;left:0;top:0;width:1200px;height:615px;background:linear-gradient(100deg,#3a4a86 0%,#5a6b9c 35%,#7d7e98 55%,#4d5a8c 80%,#2f3f7c 100%)}
.sidebar{position:absolute;left:0;top:0;width:426px;height:615px;background:rgba(45,90,43,.93)}
.side-logo{position:absolute;left:52px;top:86px;font-weight:700;font-size:52px;color:var(--white);letter-spacing:-1px}
.side-rule{position:absolute;left:39px;top:207px;width:346px;height:2px;background:var(--white)}
.nav{position:absolute;left:0;top:0;list-style:none}
.nav li{position:absolute;left:44px;width:345px;height:26px;display:flex;align-items:center;font-family:"Lato",sans-serif;font-size:16px;color:var(--white);white-space:nowrap}
.nav li svg{margin-right:20px}
.nav .drop{position:absolute;right:0;top:1px;width:24px;height:24px;background:#b8c2b6;display:flex;align-items:center;justify-content:center}
.tab-left{position:absolute;left:426px;top:261px;width:23px;height:93px;background:rgba(40,60,60,.55);display:flex;align-items:center;justify-content:center}
.tab-right{position:absolute;left:1175px;top:261px;width:25px;height:93px;background:var(--green);display:flex;align-items:center;justify-content:center}
.welcome{position:absolute;left:565px;top:190px;width:500px;text-align:center;color:var(--white);font-size:35px;font-weight:400}
.hero-title{position:absolute;left:515px;top:245px;width:600px;text-align:center;color:var(--white);font-size:94px;font-weight:700;line-height:1}
.btn-outline{background:transparent;border:2px solid var(--white)}

/* why choose */
.feature{position:absolute;top:1084px;width:240px;text-align:center}
.ring{width:148px;height:148px;margin:0 auto;border-radius:50%;background:var(--green-soft);display:flex;align-items:center;justify-content:center}
.ring-inner{width:126px;height:126px;border-radius:50%;background:var(--green);display:flex;align-items:center;justify-content:center}
.ring-core{width:86px;height:86px;border-radius:50%;background:var(--white);display:flex;align-items:center;justify-content:center}
.feature h3{margin-top:20px;font-size:22px;font-weight:600;color:var(--navy);line-height:1.15}
.feature p{margin-top:10px;font-size:15px;line-height:24px}
.feature .arrow{margin-top:12px}

/* banner */
.banner{position:absolute;left:0;top:1501px;width:1200px;height:429px;background:var(--navy-band)}
.banner h2{position:absolute;left:100px;top:84px;width:1000px;text-align:center;color:var(--white);font-size:47px;font-weight:600;line-height:56px}
.banner p{position:absolute;left:180px;top:214px;width:840px;text-align:center;color:var(--white);font-family:"Lato",sans-serif;font-weight:700;font-size:20px;line-height:29px}

/* products */
.product{position:absolute;top:2181px;width:306px;height:260px;border:2px solid var(--line);border-radius:4px;text-align:center}
.product-photo{position:absolute;left:33px;top:-73px;width:240px;height:131px}
.product h3{position:absolute;left:0;top:75px;width:100%;font-size:21px;font-weight:600;color:var(--green)}
.product p{position:absolute;left:25px;top:112px;width:254px;font-size:15px;line-height:20px}
.product .btn{left:75px;top:197px;width:154px;height:36px;font-family:"Lato",sans-serif;font-weight:700}
.circle-arrow{position:absolute;width:37px;height:37px}

/* who */
.who-photo{position:absolute;left:111px;top:2529px;width:429px;height:429px;background:linear-gradient(90deg,#8a8f98 0%,#c8ccd2 35%,#6fa5c6 55%,#d8342f 80%,#c22a28 100%)}
.who h2{position:absolute;left:616px;top:2566px}
.who p{position:absolute;left:616px;top:2652px;width:480px;font-size:15px;line-height:28.3px}

/* services */
.services{position:absolute;left:0;top:3045px;width:1200px;height:539px;background:linear-gradient(180deg,#3f6a3a,#2f5a2c 60%,#365f32)}
.services h2{position:absolute;left:0;top:86px;width:1200px;text-align:center;color:var(--white)}
.service{position:absolute;top:169px;width:305px;height:260px;background:var(--white);border-radius:3px}
.service h3{position:absolute;left:32px;top:30px;font-size:22px;font-weight:600;color:var(--navy)}
.service p{position:absolute;left:32px;top:72px;width:250px;font-size:15px;line-height:24px}
.service .btn{left:32px;top:188px;width:155px;height:36px}
.service.active{background:rgba(35,42,110,.9)}
.service.active h3,.service.active p{color:var(--white)}
.service.active .btn{background:var(--white);color:var(--navy)}

/* footer */
.foot-logo{position:absolute;left:111px;top:3700px;font-weight:700;font-size:66px;color:var(--navy);letter-spacing:-1px}
.social{position:absolute;top:3857px;width:38px;height:38px;border-radius:50%;background:var(--navy)}
.foot-col h4{position:absolute;font-size:20px;font-weight:600;color:var(--navy)}
.foot-links{position:absolute;left:586px;top:3716px;list-style:none;font-size:15px;line-height:34.3px}
.contact-item{position:absolute;left:844px;display:flex;font-size:15px;line-height:23px}
.contact-item svg{flex:none;margin-right:16px;margin-top:3px}
.copyright{position:absolute;left:0;top:3992px;width:1200px;text-align:center;font-size:12px}
</style>
</head>
<body>

<header class="hero">
  <div class="hero-photo" role="img" aria-label="Woman choosing a snack at a stocked vending machine"></div>
  <aside class="sidebar">
    <div class="side-logo">SnackOrbit</div>
    <div class="side-rule"></div>
    <ul class="nav">
      <li style="top:240px"><svg width="16" height="14" viewBox="0 0 16 14"><path d="M0 7h12M7 1l6 6-6 6" stroke="#fff" stroke-width="3" fill="none"/></svg>Home</li>
      <li style="top:291px"><svg width="16" height="14" viewBox="0 0 16 14"><path d="M0 7h12M7 1l6 6-6 6" stroke="#fff" stroke-width="3" fill="none"/></svg>About SnackOrbit</li>
      <li style="top:343px"><svg width="16" height="14" viewBox="0 0 16 14"><path d="M0 7h12M7 1l6 6-6 6" stroke="#fff" stroke-width="3" fill="none"/></svg>Why Choose SnackOrbit?</li>
      <li style="top:394px"><svg width="16" height="14" viewBox="0 0 16 14"><path d="M0 7h12M7 1l6 6-6 6" stroke="#fff" stroke-width="3" fill="none"/></svg>Products<span class="drop"><svg width="10" height="6" viewBox="0 0 10 6"><path d="M1 1l4 4 4-4" stroke="#2d5a2b" stroke-width="1.5" fill="none"/></svg></span></li>
      <li style="top:446px"><svg width="16" height="14" viewBox="0 0 16 14"><path d="M0 7h12M7 1l6 6-6 6" stroke="#fff" stroke-width="3" fill="none"/></svg>Services<span class="drop"><svg width="10" height="6" viewBox="0 0 10 6"><path d="M1 1l4 4 4-4" stroke="#2d5a2b" stroke-width="1.5" fill="none"/></svg></span></li>
      <li style="top:497px"><svg width="16" height="14" viewBox="0 0 16 14"><path d="M0 7h12M7 1l6 6-6 6" stroke="#fff" stroke-width="3" fill="none"/></svg>Contact Us</li>
    </ul>
  </aside>
  <div class="tab-left"><svg width="8" height="12" viewBox="0 0 8 12"><path d="M6 1L1 6l5 5" stroke="#ccc" stroke-width="1.5" fill="none"/></svg></div>
  <div class="tab-right"><svg width="8" height="12" viewBox="0 0 8 12"><path d="M2 1l5 5-5 5" stroke="#ddd" stroke-width="1.5" fill="none"/></svg></div>
  <div class="welcome">Welcome To</div>
  <h1 class="hero-title">SnackOrbit</h1>
  <a class="btn" style="left:652px;top:378px;width:111px;height:36px">Login</a>
  <a class="btn btn-outline" style="left:780px;top:378px;width:197px;height:36px">Get A Questionnaire</a>
</header>

<section class="about">
  <h2 class="heading abs center" style="left:0;top:700px;width:1200px">About SnackOrbit</h2>
  <p class="abs center" style="left:150px;top:774px;width:900px;font-size:15px;line-height:26px">At SnackOrbit, we don’t just vend snacks—we curate cravings. Our customized vending solutions bring flavor, convenience, and community to Northern Michigan. Whether you’re reaching for a mid-morning snack, a refreshing beverage, or a satisfying breakfast burrito, SnackOrbit delivers delight with every bite.</p>
  <a class="btn" style="left:527px;top:880px;width:146px;height:38px">Read More</a>
</section>

<section class="why">
  <h2 class="heading abs center" style="left:0;top:1000px;width:1200px">Why Choose SnackOrbit</h2>
  <div class="feature" style="left:100px">
    <div class="ring"><div class="ring-inner"><div class="ring-core"><svg width="44" height="56" viewBox="0 0 44 56"><path d="M22 53C10 38 3 29 3 21a19 19 0 0 1 38 0c0 8-7 17-19 32z" fill="none" stroke="#2d5a2b" stroke-width="3"/><path d="M22 31c-5-4-9-7-9-11a4.5 4.5 0 0 1 9-1 4.5 4.5 0 0 1 9 1c0 4-4 7-9 11z" fill="none" stroke="#2d5a2b" stroke-width="2.5"/></svg></div></div></div>
    <h3>Local Love</h3>
    <p>We celebrate the heart of Michigan by partnering with local legends.</p>
    <svg class="arrow" width="30" height="14" viewBox="0 0 30 14"><path d="M0 7h26M20 1l7 6-7 6" stroke="#2d5a2b" stroke-width="3" fill="none"/></svg>
  </div>
  <div class="feature" style="left:354px">
    <div class="ring"><div class="ring-inner"><div class="ring-core"><svg width="44" height="56" viewBox="0 0 44 56"><path d="M22 53C10 38 3 29 3 21a19 19 0 0 1 38 0c0 8-7 17-19 32z" fill="none" stroke="#2d5a2b" stroke-width="3"/><path d="M22 31c-5-4-9-7-9-11a4.5 4.5 0 0 1 9-1 4.5 4.5 0 0 1 9 1c0 4-4 7-9 11z" fill="none" stroke="#2d5a2b" stroke-width="2.5"/></svg></div></div></div>
    <h3>Unleash Your<br>Cravings</h3>
    <p>SnackOrbit isn’t bound by corporate ties. We’re the rebels of the vending world.</p>
    <svg class="arrow" width="30" height="14" viewBox="0 0 30 14"><path d="M0 7h26M20 1l7 6-7 6" stroke="#2d5a2b" stroke-width="3" fill="none"/></svg>
  </div>
  <div class="feature" style="left:607px">
    <div class="ring"><div class="ring-inner"><div class="ring-core"><svg width="44" height="56" viewBox="0 0 44 56"><path d="M22 53C10 38 3 29 3 21a19 19 0 0 1 38 0c0 8-7 17-19 32z" fill="none" stroke="#2d5a2b" stroke-width="3"/><path d="M22 31c-5-4-9-7-9-11a4.5 4.5 0 0 1 9-1 4.5 4.5 0 0 1 9 1c0 4-4 7-9 11z" fill="none" stroke="#2d5a2b" stroke-width="2.5"/></svg></div></div></div>
    <h3>Quality<br>Meets Convenience</h3>
    <p>Imagine this: You’re mid-meeting, and your stomach growls.</p>
    <svg class="arrow" width="30" height="14" viewBox="0 0 30 14"><path d="M0 7h26M20 1l7 6-7 6" stroke="#2d5a2b" stroke-width="3" fill="none"/></svg>
  </div>
  <div class="feature" style="left:861px">
    <div class="ring"><div class="ring-inner"><div class="ring-core"><svg width="44" height="56" viewBox="0 0 44 56"><path d="M22 53C10 38 3 29 3 21a19 19 0 0 1 38 0c0 8-7 17-19 32z" fill="none" stroke="#2d5a2b" stroke-width="3"/><path d="M22 31c-5-4-9-7-9-11a4.5 4.5 0 0 1 9-1 4.5 4.5 0 0 1 9 1c0 4-4 7-9 11z" fill="none" stroke="#2d5a2b" stroke-width="2.5"/></svg></div></div></div>
    <h3>Pandemic-Proof &amp;<br>Recession-Ready</h3>
    <p>Life throws curveballs, but SnackOrbit stands strong.</p>
    <svg class="arrow" width="30" height="14" viewBox="0 0 30 14"><path d="M0 7h26M20 1l7 6-7 6" stroke="#2d5a2b" stroke-width="3" fill="none"/></svg>
  </div>
</section>

<section class="banner">
  <h2>Ready to experience the SnackOrbit difference?</h2>
  <p>Sign up now and let’s connect. Taste the future of snacking firsthand! Contact us today and explore how our vending magic can elevate your space.</p>
  <a class="btn" style="left:527px;top:301px;width:146px;height:37px">Read More</a>
</section>

<section class="products">
  <h2 class="heading abs center" style="left:0;top:2012px;width:1200px">Our Products</h2>
  <svg class="circle-arrow" style="left:49px;top:2259px" viewBox="0 0 37 37"><circle cx="18.5" cy="18.5" r="17" fill="none" stroke="#1c1f5a" stroke-width="3"/><path d="M27 18.5H12M18 11l-7.5 7.5L18 26" stroke="#1c1f5a" stroke-width="4" fill="none"/></svg>
  <svg class="circle-arrow" style="left:1113px;top:2259px" viewBox="0 0 37 37"><circle cx="18.5" cy="18.5" r="17" fill="none" stroke="#1c1f5a" stroke-width="3"/><path d="M10 18.5h15M19 11l7.5 7.5L19 26" stroke="#1c1f5a" stroke-width="4" fill="none"/></svg>
  <div class="product" style="left:112px">
    <div class="product-photo" role="img" aria-label="Barista working at an espresso machine" style="background:linear-gradient(135deg,#2b2b2b,#6b625a 50%,#c7c0b5)"></div>
    <h3>Barista Coffee Machine</h3>
    <p>Excepteur sint occaecat cupidatat non proident, sunt in culpa qui mollit anim id est laborum.</p>
    <a class="btn">Add To Cart</a>
  </div>
  <div class="product" style="left:448px">
    <div class="product-photo" role="img" aria-label="Automatic vending machine in a hallway" style="background:linear-gradient(90deg,#b9bcc2,#3a4a7a 45%,#5a4a6a 60%,#c5c8cc)"></div>
    <h3>Automatic Vending Machine</h3>
    <p>Excepteur sint occaecat cupidatat non proident, sunt in culpa qui mollit anim id est laborum.</p>
    <a class="btn">Add To Cart</a>
  </div>
  <div class="product" style="left:782px">
    <div class="product-photo" role="img" aria-label="Silver espresso machine on a kitchen counter" style="background:linear-gradient(135deg,#efece8,#b9b4ad 50%,#d9d4cc)"></div>
    <h3>Silver Coffee Machine</h3>
    <p>Excepteur sint occaecat cupidatat non proident, sunt in culpa qui mollit anim id est laborum.</p>
    <a class="btn">Add To Cart</a>
  </div>
</section>

<section class="who">
  <div class="who-photo" role="img" aria-label="Woman paying by card at a drinks vending machine"></div>
  <h2 class="heading">Who We Are</h2>
  <p>Welcome to SnackOrbit, where snacking meets delight! We’re not just about vending machines; we’re your culinary companions, your flavor curators, and your secret stash of happiness.<br>Daniel and Nora, the dynamic duo behind SnackOrbit, have a passion for all things tasty. With backgrounds in sales and a penchant for personal connections, they’ve transformed the vending experience into an art form.</p>
  <a class="btn" style="left:616px;top:2880px;width:149px;height:37px">Read More</a>
</section>

<section class="services" role="img" aria-label="Vending machines in a break room with green overlay">
  <h2 class="heading">Our Services</h2>
  <svg class="circle-arrow" style="left:49px;top:277px" viewBox="0 0 37 37"><circle cx="18.5" cy="18.5" r="17" fill="none" stroke="#fff" stroke-width="3"/><path d="M27 18.5H12M18 11l-7.5 7.5L18 26" stroke="#fff" stroke-width="4" fill="none"/></svg>
  <svg class="circle-arrow" style="left:1113px;top:277px" viewBox="0 0 37 37"><circle cx="18.5" cy="18.5" r="17" fill="none" stroke="#fff" stroke-width="3"/><path d="M10 18.5h15M19 11l7.5 7.5L19 26" stroke="#fff" stroke-width="4" fill="none"/></svg>
  <div class="service" style="left:113px">
    <h3>Machines Facility</h3>
    <p>Duis aute irure dolor in reprehenderit in voluptate velit esse cillum dolore eu fugiat nulla pariatur.</p>
    <a class="btn">Read More</a>
  </div>
  <div class="service active" style="left:448px">
    <h3>Lowest Fees in City</h3>
    <p>Duis aute irure dolor in reprehenderit in voluptate velit esse cillum dolore eu fugiat nulla pariatur.</p>
    <a class="btn">Read More</a>
  </div>
  <div class="service" style="left:782px">
    <h3>Experienced Mechanics</h3>
    <p>Duis aute irure dolor in reprehenderit in voluptate velit esse cillum dolore eu fugiat nulla pariatur.</p>
    <a class="btn">Read More</a>
  </div>
</section>

<footer class="footer">
  <div class="foot-logo">SnackOrbit</div>
  <span class="social" style="left:139px"></span>
  <span class="social" style="left:200px"></span>
  <span class="social" style="left:263px"></span>
  <span class="social" style="left:329px"></span>
  <div class="foot-col">
    <h4 style="left:584px;top:3668px">Quick Links</h4>
    <ul class="foot-links">
      <li>Home</li><li>About SnackOrbit</li><li>Why Choose SnackOrbit?</li><li>Products</li><li>Services</li><li>Contact Us</li>
    </ul>
  </div>
  <div class="foot-col">
    <h4 style="left:844px;top:3668px">Contact Us</h4>
    <div class="contact-item" style="top:3703px;width:260px"><svg width="14" height="19" viewBox="0 0 14 19"><path d="M7 18C2 11 1 9 1 7a6 6 0 0 1 12 0c0 2-1 4-6 11z" fill="#1c1f5a"/><circle cx="7" cy="7" r="2.3" fill="#fff"/></svg><span>123, SnackOrbit vending machine in Northern Michigan</span></div>
    <div class="contact-item" style="top:3766px"><svg width="16" height="16" viewBox="0 0 16 16"><path d="M3 1l3 3-2 2c1 2 3 4 6 6l2-2 3 3-2 2C7 15 1 9 1 3z" fill="#1c1f5a"/></svg><span>+1 555 010 2040</span></div>
    <div class="contact-item" style="top:3800px"><svg width="17" height="13" viewBox="0 0 17 13"><rect width="17" height="13" rx="1" fill="#1c1f5a"/><path d="M1 1l7.5 6L16 1" stroke="#fff" stroke-width="1.5" fill="none"/></svg><span>info@snackorbit.com</span></div>
  </div>
  <div class="copyright">© 2024 SnackOrbit</div>
</footer>

</body>
</html>
```